Design my site www.brieflyledger.com

So here is what I am thinking in terms of design:

https://plenvo.com

https://www.skyluxair.com

http://kalvex.com/harbor-plaza-tower/

I want the theme to be white and blue (royal blue). I attached a paint picture of what I would like the site to look like in terms of placing the text. Generally, what I like about the sites above is that they are simple, you can navigate easily and have some kind of idea of what's going on by looking at the center (picture and motto). Let's establish a clear understanding of how the functional part of the site would look like. Please see the picture attached.

I want to keep it simple: On top would be the Name 'BRIEFLY ledger", somewhere to the right on top on the page would be 'Sign in" button.

In the center would be a picture (maybe a video) with the Motto (on top of it all in capital) OBSERVE NAVIGATE DECIDE and below would be the "sign up now"

Below the picture (like on kalvex.com site) or to the left on top of the page would be "About Us', "Press" "Contact Us' buttons.

Then once the user gets to his page his got 3 tabs " Press Headlines", "Events", " Briefings".

we would keep the same format I only have on the site, but separate for every Tab.

I do not want the user to get distracted. I also want him to be able to access the page though mobile phone and be able to get automatic updates just like Zorvan Pings without having to sign in daily.

The landing page must be minimalist yet with business/corporate feel where users can navigate easily and a "what you see is what you get" approach. You want an image or video (personally I prefer the video.. it does capture the users attention instantly, as long as it is an interesting video), with your taglines in it.

Sections available to public: About Us, Contact Us, Landing Page with Signup Option

Private: Public Sections + User Account Page, Tabs for (Events, Press Headlines, Briefings)

Target Market(s)

PR/media monitoring/diplomatic community

Coding

Coded - Design and coding required

Number of Pages Required

1 page

Font styles to use
Serif
Sans Serif

Colors
0255a3
ec1f27

Requirements
Must have
• a simple landing page, that is user friendly.
Nice to have
• a video with the explanation of how to navigate the site
Should not have
• too many colors, graphs etc.

```html
<!DOCTYPE html>
<html lang="en">
<head>
<meta charset="utf-8">
<title>BRIEFLY ledger</title>
<link href="https://fonts.googleapis.com/css2?family=Open+Sans:wght@400;600;700&family=Oswald:wght@500&family=Roboto:wght@400&display=swap" rel="stylesheet">
<style>
  :root{
    --blue:#2f8fc4;
    --blue-dark:#1f6e9c;
    --royal:#0255a3;
    --ink:#555555;
    --ink-dark:#333333;
    --line:#d6d6d6;
    --panel:#f4f4f4;
    --footer:#f7f7f7;
    --btn-dark:#333333;
    --white:#ffffff;
  }
  *{box-sizing:border-box;margin:0;padding:0}
  html,body{width:1200px;height:896px;overflow:hidden;background:var(--white)}
  body{position:relative;font-family:"Open Sans",Arial,sans-serif;color:var(--ink)}

  .hero{position:absolute;left:0;top:0;width:1200px;height:257px;
    background:linear-gradient(180deg,#3b4a63 0%,#4a5468 30%,#2a2f3a 65%,#1b1d22 100%)}
  .brand{position:absolute;left:98px;top:40px;width:313px;height:57px;background:var(--white);
    border:2px solid var(--blue);display:flex;align-items:center;justify-content:center;
    font-family:"Oswald",sans-serif;font-weight:500;font-size:34px;color:var(--blue);letter-spacing:.5px}
  .sign-in{position:absolute;left:982px;top:52px;width:83px;height:32px;background:var(--blue);
    border:1px solid #8ccbee;border-radius:4px;color:var(--white);font-weight:700;font-size:14px;
    display:flex;align-items:center;justify-content:center}
  .menu-icon{position:absolute;left:1079px;top:58px}

  .tabs{position:absolute;left:98px;top:296px;width:1003px;height:42px;border-bottom:1px solid var(--blue)}
  .tab{position:absolute;top:0;height:41px;font-size:16px;font-weight:600;color:#666;
    display:flex;align-items:center;justify-content:center;letter-spacing:.2px}
  .tab.active{left:0;width:206px;background:var(--blue);color:var(--white)}
  .tab.events{left:260px;width:120px}
  .tab.briefings{left:480px;width:123px}

  .panel{position:absolute;left:98px;top:338px;width:1003px;height:381px;background:var(--panel);
    border:1px solid #e2e2e2;border-top:none}
  .label{position:absolute;font-size:13.5px;color:var(--ink)}
  .field{position:absolute;width:347px;height:35px;background:var(--white);border:1px solid var(--line);border-radius:2px}
  .field::after{content:"";position:absolute;right:35px;top:4px;bottom:4px;border-left:1px solid #ececec}
  .select{font-size:10.5px;color:#666;padding-left:11px;display:flex;align-items:center}
  .select::after{top:0;bottom:0;border-color:var(--line)}
  .caret{position:absolute;right:13px;top:15px}

  .btn{position:absolute;top:276px;height:37px;font-family:"Roboto",sans-serif;font-size:15.5px;color:var(--white);
    display:flex;align-items:center;justify-content:center;border-radius:1px}
  .btn.submit{left:50px;width:128px;background:var(--blue)}
  .btn.report{left:187px;width:179px;background:var(--btn-dark)}

  .sources{position:absolute;left:425px;top:78px;width:347px;height:172px;background:var(--white);border:1px solid var(--line)}
  .sources-head{height:35px;border-bottom:1px solid var(--line);display:flex;align-items:center;padding-left:16px;font-size:10.5px;color:#666;gap:10px}
  .source-list{list-style:none;position:absolute;left:16px;top:49px}
  .source-list li{height:23px;display:flex;align-items:center;gap:10px;font-size:11.5px;color:var(--ink-dark)}
  .scrollbar{position:absolute;right:0;top:36px;width:18px;height:135px;background:#f1f1f1}
  .thumb{position:absolute;left:4px;top:19px;width:11px;height:37px;background:#c1c1c1}

  .footer{position:absolute;left:0;top:785px;width:1200px;height:111px;background:var(--footer);border-top:1px solid #e6e6e6}
  .footer-nav{position:absolute;left:98px;top:37px;font-size:12.5px;font-weight:600;color:var(--blue);display:flex;gap:11px}
  .footer-nav .sep{color:#444;font-weight:400}
  .copyright{position:absolute;left:98px;top:64px;font-size:12.5px;color:var(--ink-dark)}
  .social{position:absolute;left:926px;top:35px;display:flex;gap:8.5px}
  .social span{width:28px;height:28px;border-radius:50%;background:var(--blue);display:block}
</style>
</head>
<body>
  <header class="hero" role="img" aria-label="Dusk aerial photograph of a city skyline with towers and lights">
    <div class="brand">BRIEFLY LEDGER</div>
    <div class="sign-in">SIGN IN</div>
    <svg class="menu-icon" width="22" height="19" viewBox="0 0 22 19" aria-hidden="true">
      <rect y="0" width="22" height="3.5" fill="#fff"/><rect y="7.7" width="22" height="3.5" fill="#fff"/><rect y="15.5" width="22" height="3.5" fill="#fff"/>
    </svg>
  </header>

  <nav class="tabs">
    <div class="tab active">PRESS HEADLINES</div>
    <div class="tab events">EVENTS</div>
    <div class="tab briefings">BRIEFINGS</div>
  </nav>

  <section class="panel">
    <div class="label" style="left:49px;top:54px">Keywords :</div>
    <div class="field" style="left:49px;top:78px"></div>
    <div class="label" style="left:49px;top:122px">Authors :</div>
    <div class="field" style="left:49px;top:146px"></div>
    <div class="label" style="left:49px;top:191px">Date range :</div>
    <div class="field select" style="left:49px;top:215px">Past 24 hours
      <svg class="caret" width="9" height="5" viewBox="0 0 9 5" aria-hidden="true"><path d="M0 0h9L4.5 5z" fill="#555"/></svg>
    </div>

    <div class="btn submit">SUBMIT</div>
    <div class="btn report">DOWNLOAD REPORT</div>

    <div class="label" style="left:425px;top:54px">All Sources :</div>
    <div class="sources">
      <div class="sources-head">
        <svg width="11" height="11" viewBox="0 0 11 11" aria-hidden="true"><rect x=".5" y=".5" width="10" height="10" rx="1.5" fill="#eee" stroke="#999"/><path d="M2.5 5.5l2 2 4-4.5" fill="none" stroke="#333" stroke-width="1.5"/></svg>
        All Sources
      </div>
      <ul class="source-list">
        <li><svg width="11" height="11" viewBox="0 0 11 11" aria-hidden="true"><rect x=".5" y=".5" width="10" height="10" rx="1.5" fill="#eee" stroke="#999"/><path d="M2.5 5.5l2 2 4-4.5" fill="none" stroke="#333" stroke-width="1.5"/></svg>Capitol Courier</li>
        <li><svg width="11" height="11" viewBox="0 0 11 11" aria-hidden="true"><rect x=".5" y=".5" width="10" height="10" rx="1.5" fill="#eee" stroke="#999"/><path d="M2.5 5.5l2 2 4-4.5" fill="none" stroke="#333" stroke-width="1.5"/></svg>Empire Daily Times</li>
        <li><svg width="11" height="11" viewBox="0 0 11 11" aria-hidden="true"><rect x=".5" y=".5" width="10" height="10" rx="1.5" fill="#eee" stroke="#999"/><path d="M2.5 5.5l2 2 4-4.5" fill="none" stroke="#333" stroke-width="1.5"/></svg>Brackwell</li>
        <li><svg width="11" height="11" viewBox="0 0 11 11" aria-hidden="true"><rect x=".5" y=".5" width="10" height="10" rx="1.5" fill="#eee" stroke="#999"/><path d="M2.5 5.5l2 2 4-4.5" fill="none" stroke="#333" stroke-width="1.5"/></svg>The Sentinel's</li>
        <li><svg width="11" height="11" viewBox="0 0 11 11" aria-hidden="true"><rect x=".5" y=".5" width="10" height="10" rx="1.5" fill="#eee" stroke="#999"/><path d="M2.5 5.5l2 2 4-4.5" fill="none" stroke="#333" stroke-width="1.5"/></svg>Potomac Herald</li>
      </ul>
      <div class="scrollbar">
        <svg style="position:absolute;left:5px;top:5px" width="8" height="5" viewBox="0 0 8 5" aria-hidden="true"><path d="M0 5h8L4 0z" fill="#666"/></svg>
        <div class="thumb"></div>
        <svg style="position:absolute;left:5px;bottom:5px" width="8" height="5" viewBox="0 0 8 5" aria-hidden="true"><path d="M0 0h8L4 5z" fill="#666"/></svg>
      </div>
    </div>
  </section>

  <footer class="footer">
    <nav class="footer-nav"><span>ABOUT US</span><span class="sep">/</span><span>PRESS</span><span class="sep">/</span><span>CONTACT US</span></nav>
    <p class="copyright">2016 © Copyrights BRIEFLY ledger.All Rights Reserved</p>
    <div class="social" aria-label="Social links"><span></span><span></span><span></span><span></span><span></span></div>
  </footer>
</body>
</html>
```